Car transport business

We need a new business card design. Attached is our old card sample. I would just like to adjust the logo colors (blue and red) to be brighter. I changed my name to the brighter red and the word dispatcher to a brighter blue as an example. But you can adjust those colors further. And then perhaps you can use the same colors for the card design but use your imagination.

As a suggestion so the card stands out I would like to add a clip art of car carrier truck. Attached are examples of that as well

```html
<!DOCTYPE html>
<html lang="en">
<head>
<meta charset="utf-8">
<title>Northline Haul — Business Card</title>
<link href="https://fonts.googleapis.com/css2?family=Arimo:wght@400;700&display=swap" rel="stylesheet">
<style>
  :root {
    --backdrop: #0e0e0f;
    --card: #2a2a2c;
    --card-edge: #e0202a;
    --brand-blue: #1e73d2;
    --brand-red: #ee1c25;
    --text-light: #e9e9ea;
    --rule: #4a4a4d;
    --emboss: #3a3a3d;
  }
  * { box-sizing: border-box; margin: 0; padding: 0; }
  html, body {
    width: 1200px; height: 820px; overflow: hidden;
    background: var(--backdrop);
    font-family: "Arimo", Arial, sans-serif;
  }
  .stage {
    width: 1200px; height: 820px;
    display: flex; align-items: center; justify-content: center; gap: 60px;
  }
  .card {
    position: relative;
    width: 520px; height: 297px;
    background: var(--card);
    border: 3px solid var(--card-edge);
    border-radius: 2px;
    overflow: hidden;
  }
  .wordmark {
    position: absolute;
    display: flex; flex-direction: column; align-items: flex-start;
  }
  .wordmark__name {
    font-weight: 700; font-size: 34px; letter-spacing: 1px;
    color: var(--brand-blue); line-height: 1; text-transform: uppercase;
  }
  .wordmark__tagline {
    margin-top: 6px;
    font-weight: 400; font-size: 10px; letter-spacing: 3.2px;
    color: var(--brand-blue); text-transform: uppercase;
  }
  .wordmark__dot {
    position: absolute; left: -40px; top: 2px;
    width: 30px; height: 30px; border-radius: 50%;
    background: var(--brand-red);
  }

  /* contact side */
  .card--contact .wordmark { left: 172px; top: 60px; }
  .divider {
    position: absolute; left: 200px; right: 24px; top: 190px;
    height: 1px; background: var(--rule);
  }
  .person { position: absolute; left: 28px; top: 168px; }
  .person__name {
    font-size: 24px; font-weight: 400; letter-spacing: 0.5px; line-height: 1;
    text-transform: uppercase;
  }
  .person__first { color: var(--brand-blue); }
  .person__last { color: var(--brand-red); }
  .person__role {
    margin-top: 4px; font-size: 13px; color: var(--text-light); letter-spacing: 0.5px;
  }
  .contact-list { list-style: none; margin-top: 12px; }
  .contact-list li {
    display: flex; align-items: center; gap: 9px;
    font-size: 14px; color: var(--text-light); line-height: 20px;
  }
  .contact-list svg { width: 14px; height: 14px; fill: var(--brand-blue); flex: none; }

  /* brand side */
  .card--brand .emboss {
    position: absolute; left: 40px; top: 30px;
    width: 200px; height: 200px; border-radius: 50%;
    border: 14px solid var(--emboss);
  }
  .card--brand .wordmark { left: 250px; top: 170px; }
  .card--brand .wordmark__name { font-size: 30px; }
  .card--brand .wordmark__tagline { font-size: 9px; letter-spacing: 2.6px; }
</style>
</head>
<body>
<main class="stage">

  <section class="card card--contact" aria-label="Card front with contact details">
    <div class="wordmark">
      <span class="wordmark__dot"></span>
      <span class="wordmark__name">Northline Haul</span>
      <span class="wordmark__tagline">The Auto Transport Professionals</span>
    </div>
    <div class="divider"></div>
    <div class="person">
      <p class="person__name"><span class="person__first">Ravi</span> <span class="person__last">Lannert</span></p>
      <p class="person__role">DISPATCHER</p>
      <ul class="contact-list">
        <li>
          <svg viewBox="0 0 24 24" aria-hidden="true"><path d="M6.6 10.8a15 15 0 0 0 6.6 6.6l2.2-2.2a1 1 0 0 1 1-.25 11.4 11.4 0 0 0 3.6.57 1 1 0 0 1 1 1V20a1 1 0 0 1-1 1A17 17 0 0 1 3 4a1 1 0 0 1 1-1h3.5a1 1 0 0 1 1 1c0 1.25.2 2.45.57 3.57a1 1 0 0 1-.25 1z"/></svg>
          555-014-2201
        </li>
        <li>
          <svg viewBox="0 0 24 24" aria-hidden="true"><path d="M6 2h12v5H6zM4 8h16a2 2 0 0 1 2 2v7h-4v5H6v-5H2v-7a2 2 0 0 1 2-2zm4 8v4h8v-4z"/></svg>
          555-014-2277
        </li>
        <li>
          <svg viewBox="0 0 24 24" aria-hidden="true"><path d="M2 5h20v14H2zm2 2v.5l8 5 8-5V7zm0 2.8V17h16V9.8l-8 5z"/></svg>
          northlinehaul@example.com
        </li>
      </ul>
    </div>
  </section>

  <section class="card card--brand" aria-label="Card back with company name">
    <div class="emboss" aria-hidden="true"></div>
    <div class="wordmark">
      <span class="wordmark__name">Northline Haul</span>
      <span class="wordmark__tagline">The Auto Transport Professionals</span>
    </div>
  </section>

</main>
</body>
</html>
```